Modern Medical Optometry Website

We need mordern, Patient friendly website. Easy to navigate and enhance our advance medical technology and excellent patient care.
1. HOME PAGE
2. OUR TEAM PAGE
3. EYECARE PAGE - VISION SERVICES, EYE EXAMS, KERATOCONUS CENTER, GLAUCOMA , DIABITES, MELORIDEX EXAM, DIGITAL RETINAL, OCT.
4. MYOPIA CONTROL CLINIC
5. DRY EYE CLINIC
6. EYEWEAR
7. PATIENT CENTER - BLOG
7. CONTACT US
This is our current website www.brivaloka.com
and We want to add more content and a cleaner design like these website
http://tarnwickfolvendale.com/
https://www.qmvorlu.com/

```html
<!DOCTYPE html>
<html lang="en">
<head>
<meta charset="utf-8">
<title>Lumivane Optometry</title>
<link href="https://fonts.googleapis.com/css2?family=Lato:ital,wght@0,400;0,700;0,900;1,700&family=Ubuntu:wght@400;500;700&display=swap" rel="stylesheet">
<style>
:root{
  --teal:#5bd6dc;
  --navy:#0d1433;
  --ink:#1c1c1c;
  --grey:#555;
  --tile:#ededed;
  --white:#fff;
}
*{box-sizing:border-box;margin:0;padding:0}
html,body{width:1200px;height:3965px;overflow:hidden}
body{position:relative;background:var(--white);font-family:"Lato",sans-serif;color:var(--ink)}
.abs{position:absolute}

/* header */
.brand{left:105px;top:18px;width:120px;display:flex;flex-direction:column;align-items:center;gap:6px}
.brand-mark{width:54px;height:54px;background:#f2c230}
.brand-name{font-family:"Lato",sans-serif;font-weight:700;font-size:13px;color:#f2c230;letter-spacing:1px;text-align:center;line-height:1.2}
.contact{top:38px;display:flex;align-items:center;gap:14px;font-family:"Ubuntu",sans-serif}
.contact .ico{width:40px;height:40px;border-radius:50%;border:2px solid var(--teal);display:flex;align-items:center;justify-content:center}
.contact small{display:block;font-size:12px;color:#333}
.contact b{font-size:16px;font-weight:500;color:#111}
.appt{left:864px;top:37px;width:222px;height:48px;border-radius:24px;background:var(--navy);color:#fff;font-family:"Ubuntu",sans-serif;font-weight:500;font-size:17px;display:flex;align-items:center;justify-content:center}
.nav{left:0;top:122px;width:1200px;height:44px;background:var(--teal);display:flex;justify-content:center;align-items:center;gap:28px;font-family:"Ubuntu",sans-serif;font-weight:500;font-size:15px;color:#111}

/* hero */
.hero{left:0;top:166px;width:1200px;height:620px}
.hero-title{left:520px;top:300px;font-family:"Lato",sans-serif;font-size:60px;font-weight:400;color:#1d1d1d;white-space:nowrap}
.hero-sub{left:522px;top:388px;width:520px;font-family:"Ubuntu",sans-serif;font-size:25px;color:#222;line-height:1.25}
.hero-btn{left:520px;top:507px;width:212px;height:48px;border:3px solid #1d1d1d;border-radius:24px;font-family:"Ubuntu",sans-serif;font-weight:700;font-size:17px;display:flex;align-items:center;justify-content:center}

/* promise */
.section-title{width:1200px;left:0;text-align:center;font-family:"Lato",sans-serif;font-weight:700;font-size:42px;letter-spacing:.5px}
.tiles{left:111px;top:1047px;width:975px;display:grid;grid-template-columns:repeat(3,317px);gap:16px 12px}
.tile{height:330px;background:var(--tile);position:relative}
.tile .photo{height:245px}
.tile .badge{position:absolute;left:50%;top:217px;width:56px;height:56px;margin-left:-28px;border-radius:50%;background:#fff;display:flex;align-items:center;justify-content:center}
.tile .label{position:absolute;left:0;right:0;bottom:8px;text-align:center;font-family:"Lato",sans-serif;font-weight:700;font-size:31px;letter-spacing:.5px}
.tile.active{background:var(--teal)}

/* testimonials */
.testi-title{color:#fff;top:2034px}
.card{top:2130px;width:423px;height:352px;background:#fff;border:4px solid var(--teal);text-align:center;padding:50px 20px 0}
.card .quote{position:absolute;left:24px;top:-22px;width:60px;height:52px;border-radius:0 0 30px 30px;background:var(--teal);display:flex;align-items:center;justify-content:center}
.card p{font-family:"Lato",sans-serif;font-style:italic;font-weight:700;font-size:16px;line-height:25px;color:#111}
.card .avatar{width:98px;height:98px;border-radius:50%;margin:18px auto 14px;background:radial-gradient(circle at 50% 40%,#8a5a44,#3a2a25)}
.card .name{font-family:"Lato",sans-serif;font-weight:900;font-size:16px;letter-spacing:.5px}
.arrow{top:2285px}

/* about */
.about-title{top:2598px}
.about-text{left:211px;top:2678px;width:779px;text-align:center;font-family:"Lato",sans-serif;font-size:15px;line-height:26px;color:#444}
.btn-dark{left:510px;top:2852px;width:180px;height:48px;border-radius:24px;background:var(--navy);color:#fff;font-family:"Ubuntu",sans-serif;font-weight:500;font-size:17px;display:flex;align-items:center;justify-content:center}

/* locations */
.map{left:0;top:3140px;width:1200px;height:600px;background:linear-gradient(135deg,#eef0e6 0%,#e4e7dc 40%,#dfe9d4 70%,#eceee4 100%)}
.info{top:3029px;width:317px;height:235px;padding:26px 22px;font-family:"Ubuntu",sans-serif;font-size:15px;line-height:24px;color:#111}
.info h3{font-family:"Ubuntu",sans-serif;font-weight:700;font-size:20px;margin-bottom:14px}
.info.teal{background:var(--teal)}
.info.navy{background:var(--navy);color:#fff}

/* footer */
.footer{left:0;top:3590px;width:1200px;height:375px}
.news-title{top:3680px;color:#fff;font-size:30px}
.news-form{left:402px;top:3753px;display:flex}
.news-form .field{width:272px;height:45px;background:#fff;font-family:"Lato",sans-serif;font-style:italic;font-size:13px;color:#777;padding:14px 26px}
.news-form .go{width:124px;height:45px;background:var(--teal);color:#fff;font-family:"Ubuntu",sans-serif;font-weight:700;font-size:14px;display:flex;align-items:center;justify-content:center}
.socials{left:538px;top:3851px;width:124px;display:flex;justify-content:space-between}
.socials span{width:12px;height:12px;border-radius:50%;background:#fff}
.copy{top:3924px;width:1200px;left:0;text-align:center;color:#fff;font-family:"Lato",sans-serif;font-size:12px}
</style>
</head>
<body>

<!-- header -->
<div class="abs brand">
  <div class="brand-mark"></div>
  <div class="brand-name">LUMIVANE<br>OPTOMETRY</div>
</div>
<div class="abs contact" style="left:350px">
  <div class="ico"><svg width="18" height="18" viewBox="0 0 24 24"><path d="M6.6 10.8a15 15 0 0 0 6.6 6.6l2.2-2.2c.3-.3.7-.4 1-.2 1.1.4 2.3.6 3.6.6.6 0 1 .4 1 1V20c0 .6-.4 1-1 1A17 17 0 0 1 3 4c0-.6.4-1 1-1h3.5c.6 0 1 .4 1 1 0 1.300.2 2.5.6 3.6.1.3 0 .7-.2 1z" fill="#111"/></svg></div>
  <div><small>Call Us :</small><b>888 555 0142</b></div>
</div>
<div class="abs contact" style="left:555px">
  <div class="ico"><svg width="18" height="14" viewBox="0 0 24 18"><rect x="1" y="1" width="22" height="16" rx="2" fill="#111"/><path d="M2 2l10 8 10-8" stroke="#fff" stroke-width="2" fill="none"/></svg></div>
  <div><small>Email :</small><b>lumivanecare@gmail.com</b></div>
</div>
<div class="abs appt">Make An Appointment</div>

<nav class="abs nav">
  <span>HOME</span><span>OUR TEAM</span><span>EYECARE</span><span>MYOPIA CONTROL CLINIC</span><span>DRY EYE CLINIC</span><span>EYEWEAR</span><span>PATIENT CENTER</span><span>CONTACT US</span>
</nav>

<!-- hero -->
<svg class="abs hero" viewBox="0 0 1200 620" role="img" aria-label="Smiling woman wearing glasses beside a coastal field">
  <defs>
    <linearGradient id="heroSky" x1="0" y1="0" x2="1" y2="1">
      <stop offset="0" stop-color="#b9b2a8"/>
      <stop offset=".35" stop-color="#dfe2e4"/>
      <stop offset=".65" stop-color="#b5b797"/>
      <stop offset="1" stop-color="#6f7454"/>
    </linearGradient>
  </defs>
  <rect width="1200" height="620" fill="url(#heroSky)"/>
  <path d="M0 470 Q600 740 1200 440 L1200 620 L0 620 Z" fill="#fff"/>
</svg>
<div class="abs hero-title">Lumivane Optometry</div>
<div class="abs hero-sub">A Fast and Effective at Home Treatment For Dry Eye Disease</div>
<div class="abs hero-btn">CONTACT US</div>
<svg class="abs" style="left:586px;top:704px" width="28" height="44" viewBox="0 0 28 44"><rect x="2" y="2" width="24" height="40" rx="12" fill="none" stroke="var(--teal)" stroke-width="3"/><path d="M9 14l5 4 5-4M9 22l5 4 5-4M9 30l5 4 5-4" stroke="var(--teal)" stroke-width="2" fill="none"/></svg>

<!-- promise -->
<h2 class="abs section-title" style="top:896px">THE LUMIVANE PROMISE</h2>
<svg class="abs" style="left:577px;top:962px" width="46" height="30" viewBox="0 0 46 30"><path d="M2 15Q23-6 44 15Q23 36 2 15Z" fill="none" stroke="var(--teal)" stroke-width="3"/><circle cx="23" cy="15" r="7" fill="var(--teal)"/></svg>

<div class="abs tiles">
  <div class="tile">
    <div class="photo" role="img" aria-label="Clinic team standing together in the office" style="background:linear-gradient(180deg,#c9c35a,#3a4a66)"></div>
    <div class="badge"><svg width="28" height="22" viewBox="0 0 28 22"><circle cx="14" cy="6" r="5" fill="#111"/><circle cx="5" cy="8" r="3.5" fill="#111"/><circle cx="23" cy="8" r="3.5" fill="#111"/><path d="M6 22q0-9 8-9t8 9z M0 20q0-6 5-6t5 3l-2 3z M28 20q0-6-5-6t-5 3l2 3z" fill="#111"/></svg></div>
    <div class="label">TEAM</div>
  </div>
  <div class="tile active">
    <div class="photo" role="img" aria-label="Tired office worker rubbing her eyes" style="background:linear-gradient(180deg,#e6e6e6,#9a9a9a)"></div>
    <div class="badge"><svg width="30" height="18" viewBox="0 0 30 18"><path d="M1 9Q15-5 29 9Q15 23 1 9Z" fill="#111"/><circle cx="15" cy="9" r="4" fill="#fff"/></svg></div>
    <div class="label">DRY EYES</div>
  </div>
  <div class="tile">
    <div class="photo" role="img" aria-label="Paper shopping bag with eyewear promotion" style="background:linear-gradient(180deg,#e8e4dc,#a5804f)"></div>
    <div class="badge"><svg width="24" height="24" viewBox="0 0 24 24"><circle cx="12" cy="12" r="11" fill="#111"/><path d="M5 8q4 1 5 5t-1 7M14 3q0 5 4 6t4 4" stroke="#fff" stroke-width="2" fill="none"/></svg></div>
    <div class="label">SOCIAL</div>
  </div>
  <div class="tile">
    <div class="photo" role="img" aria-label="Rows of optical trial lenses" style="background:linear-gradient(180deg,#c2beb6,#8f8a7e)"></div>
    <div class="badge"><svg width="26" height="26" viewBox="0 0 26 26"><path d="M1 12Q13-4 25 12Z" fill="#111"/><path d="M13 12v9q0 3-3 3t-3-3" stroke="#111" stroke-width="2.4" fill="none"/></svg></div>
    <div class="label">INSURANCE</div>
  </div>
  <div class="tile">
    <div class="photo" role="img" aria-label="Patient during an eye examination" style="background:linear-gradient(180deg,#d8dfe6,#6f8190)"></div>
    <div class="badge"><svg width="20" height="24" viewBox="0 0 20 24"><path d="M2 1h11l5 5v17H2z" fill="none" stroke="#111" stroke-width="2"/><path d="M5 11h10M5 15h10M5 19h7" stroke="#111" stroke-width="2"/></svg></div>
    <div class="label">EXAM</div>
  </div>
  <div class="tile">
    <div class="photo" role="img" aria-label="Woman wearing dark framed glasses" style="background:linear-gradient(180deg,#c89a72,#5a3a2a)"></div>
    <div class="badge"><svg width="26" height="20" viewBox="0 0 26 20"><path d="M1 1h10v10l-5 8H2l4-8H1zM15 1h10v10l-5 8h-4l4-8h-5z" fill="#111"/></svg></div>
    <div class="label">TESTIMONIALS</div>
  </div>
</div>

<!-- testimonials band -->
<svg class="abs" style="left:0;top:1780px" width="1200" height="620" viewBox="0 0 1200 620">
  <path d="M0 10 Q600 240 1200 10 L1200 595 Q1080 480 1060 440 L140 440 Q120 480 0 595 Z" fill="var(--teal)"/>
</svg>
<h2 class="abs section-title testi-title">TESTIMONIALS</h2>
<div class="abs card" style="left:143px">
  <div class="quote"><svg width="34" height="24" viewBox="0 0 26 20"><path d="M1 1h10v10l-5 8H2l4-8H1zM15 1h10v10l-5 8h-4l4-8h-5z" fill="#fff"/></svg></div>
  <p>Lorem ipsum dolor sit amet, consectetur<br>iscing elit, sed do eiusmod tempor incididunt<br>ut labore et dolore magna aliqua. Ut enim<br>ad minim veniam, quis</p>
  <div class="avatar" role="img" aria-label="Portrait of the reviewer"></div>
  <div class="name">LENA MARSH</div>
</div>
<div class="abs card" style="left:632px">
  <div class="quote"><svg width="34" height="24" viewBox="0 0 26 20"><path d="M1 1h10v10l-5 8H2l4-8H1zM15 1h10v10l-5 8h-4l4-8h-5z" fill="#fff"/></svg></div>
  <p>Lorem ipsum dolor sit amet, consectetur<br>iscing elit, sed do eiusmod tempor incididunt<br>ut labore et dolore magna aliqua. Ut enim<br>ad minim veniam, quis</p>
  <div class="avatar" role="img" aria-label="Portrait of the reviewer" style="background:radial-gradient(circle at 50% 40%,#6a5040,#1a1a1a)"></div>
  <div class="name">TARA QUILL</div>
</div>
<svg class="abs arrow" style="left:40px" width="24" height="40" viewBox="0 0 24 40"><path d="M20 4L4 20l16 16" stroke="#fff" stroke-width="5" fill="none"/></svg>
<svg class="abs arrow" style="left:1134px" width="24" height="40" viewBox="0 0 24 40"><path d="M4 4l16 16L4 36" stroke="#fff" stroke-width="5" fill="none"/></svg>

<!-- about -->
<h2 class="abs section-title about-title">ABOUT US</h2>
<p class="abs about-text">Sed ut perspiciatis unde omnis iste natus error sit voluptatem accusantium doloremque laudantium, totam rem aperiam, eaque ipsa quae ab illo inventore veritatis et quasi architecto beatae vitae dicta sunt explicabo. Nemo enim ipsam voluptatem quia voluptas sit aspernatur aut odit aut fugit, sed quia consequuntur magni dolores eos qui ratione voluptatem sequi nesciunt. Neque porro quisquam est, qui dolorem ipsum quia dolor sit amet, consectetur, adipisci velit, sed quia non numquam eius modi tempora incidunt ut labore et dolore magnam aliquam quaerat voluptatem</p>
<div class="abs btn-dark">Read More</div>

<!-- locations -->
<div class="abs map" role="img" aria-label="Street map showing both clinic locations"></div>
<div class="abs info teal" style="left:111px">
  <h3>Lumivane Optometry</h3>
  4410 Corvell Ave.,<br>Corvell Park, CA 90712<br>Phone. 818-555-0110<br>Fax. 818-555-0170<br>Email. info@lumivane.com
</div>
<div class="abs info navy" style="left:441px">
  <h3>Ormond Hills</h3>
  2285 Ormond St.,<br>Suite 12,<br>Ormond Hills, CA 90788<br>Phone. 818-555-0420<br>Email. ormondhills@lumivane.com
</div>
<div class="abs info teal" style="left:769px;font-size:14px;line-height:22px">
  <h3>Opening Hours</h3>
  Monday - Thursday: 9 am - 6 pm<br>Friday: 8.30 am - 5 pm<br>Saturday: 8.30 am - 5 pm<br>Closed on Sundays<br>Please keep in mind we are closed for lunch 1-2 pm
</div>

<!-- footer -->
<svg class="abs footer" viewBox="0 0 1200 375">
  <path d="M0 150 Q600 -40 1200 150 L1200 375 L0 375 Z" fill="var(--navy)"/>
</svg>
<h2 class="abs section-title news-title">NEWSLETTER</h2>
<div class="abs news-form">
  <div class="field">Enter Your Email Address</div>
  <div class="go">SUBSCRIBE</div>
</div>
<div class="abs socials"><span></span><span></span><span></span><span></span></div>
<p class="abs copy">© 2019 All Rights Reserved Terms of Use and Privacy Policy</p>

</body>
</html>
```